Fitness website

Website for a fitness brand (see attached specs). Design needs to be modern and vibrant with CTAs on every page. We will provide logos, images, etc but for now user placeholder text and images. For now use the name 'Corvane Athletics' as the name to use on the design. The goal of this site is to either get people to join the gym (5 physical locations across the US); buy an online program; buy merch or supplements or sign up for the newsletter. Pleas use images from this foldeR: https://filebarn.example/share/folders/8QwTz41mKpLrXv93NdYe7HsaBuJ0Cf2_R?usp=sharing

We will be coding this in ReactNative. Lots more work for the winner as well, this is a 1st project for us.

Target Market(s)

fitness enthusiats

Industry/Entity Type

fitness, health, wellness

Number of Pages Required

5+ page

Font styles to use
Other font styles liked:
• Lato

Colors
0054AA
0677BA
7BADD7
CADEEF
E8F1F8
0094D4
00A9DD
6FCCEA
C7EBF8
E9F6FB
00AB8E
00BBA5
67D7C9
C6EFE9
E9F9F6
EE7325
F08F49
F5BC92
FAE3D3
FDF4ED

Requirements
Must have
• must be reactive. most people will view it first on mobile
Nice to have
• video in hero section of top of home page

```html
<!DOCTYPE html>
<html lang="en">
<head>
<meta charset="utf-8">
<title>Corvane Athletics</title>
<link href="https://fonts.googleapis.com/css2?family=Outfit:wght@400;500;600;700&family=Lato:wght@400;700;900&display=swap" rel="stylesheet">
<style>
:root{
  --navy:#0a1730;
  --navy-2:#0e1d3a;
  --band:#1f3e72;
  --yellow:#fdd20a;
  --cream:#fbf9e8;
  --green:#149a3a;
  --ink:#111820;
  --muted:#c8cfdc;
  --white:#ffffff;
}
*{box-sizing:border-box;margin:0;padding:0}
html,body{width:1200px;height:4138px;overflow:hidden;background:var(--navy)}
body{font-family:"Lato",sans-serif;color:var(--white);position:relative}
h1,h2,h3,h4,.brand{font-family:"Outfit",sans-serif}
.abs{position:absolute}
.arr{width:22px;height:22px;flex:none}
.btn{display:inline-flex;align-items:center;gap:10px;height:40px;padding:0 6px 0 20px;border-radius:20px;font-family:"Outfit",sans-serif;font-weight:600;font-size:11px;letter-spacing:.02em;text-transform:uppercase}
.btn-yellow{background:var(--yellow);color:var(--ink)}
.btn-yellow .arr circle{fill:var(--ink)}
.btn-yellow .arr path{stroke:var(--yellow)}
.btn-ghost{border:1.5px solid var(--white);color:var(--white)}
.btn-ghost .arr circle{fill:var(--white)}
.btn-ghost .arr path{stroke:var(--navy)}
.arr path{fill:none;stroke-width:1.8;stroke-linecap:round;stroke-linejoin:round}

/* header */
.topbar{position:absolute;top:0;left:0;width:1200px;height:80px;z-index:3}
.topbar .brand{left:120px;top:28px;font-weight:700;font-size:19px;color:var(--white)}
.nav{position:absolute;left:376px;top:34px;display:flex;gap:24px;font-family:"Outfit",sans-serif;font-size:11px;font-weight:600}
.nav span.dd::after{content:"";display:inline-block;width:5px;height:5px;border-right:1.3px solid #fff;border-bottom:1.3px solid #fff;transform:rotate(45deg);margin:0 0 3px 7px}
.icon-btn{position:absolute;top:29px;width:24px;height:24px;border:1.5px solid #fff;border-radius:50%}
.join{position:absolute;left:966px;top:25px;height:32px;padding:0 4px 0 16px}

/* hero */
.hero{position:absolute;top:0;left:0;width:1200px;height:666px;background:linear-gradient(100deg,#121a2a 0%,#1d2636 38%,#3a4354 62%,#222a38 100%)}
.hero h1{position:absolute;left:120px;top:190px;font-size:58px;line-height:62px;font-weight:600}
.hero h1 em{font-style:normal;color:var(--yellow)}
.hero p{position:absolute;left:122px;top:392px;font-size:17px;line-height:22px;color:#eef1f6;width:400px}
.hero .b1{position:absolute;left:122px;top:462px}
.hero .b2{position:absolute;left:302px;top:462px}
.play{position:absolute;left:1024px;top:553px;width:40px;height:40px;border-radius:50%;background:#fff;box-shadow:0 0 0 6px rgba(255,255,255,.25)}

/* about */
.about-photo{left:122px;top:718px;width:548px;height:361px;border:4px solid var(--yellow);border-radius:10px;background:linear-gradient(160deg,#3a3f4a,#15181f 70%)}
.about-card{left:690px;top:718px;width:387px;height:361px;background:var(--cream);border-radius:10px;color:var(--ink);padding:20px 28px}
.about-card h2{font-size:35px;line-height:40px;font-weight:500;margin-bottom:14px}
.about-card p{font-size:10.4px;line-height:16.5px;margin-bottom:14px}
.features{left:120px;top:1116px;width:960px;display:flex;justify-content:space-between}
.feat{display:flex;gap:10px;width:238px}
.ring{width:66px;height:66px;border-radius:50%;border:3px solid var(--yellow);display:flex;align-items:center;justify-content:center;flex:none}
.feat h4{font-size:15px;font-weight:600;margin:6px 0 3px}
.feat p{font-size:10.4px;line-height:14px;color:#dfe4ee}

/* programs */
.programs{left:0;top:1250px;width:1200px;height:536px;background:linear-gradient(180deg,#1d3a6a,#23467e 50%,#1d3a6a)}
.programs h2{position:absolute;top:48px;width:1200px;text-align:center;font-size:32px;font-weight:500}
.prog{position:absolute;top:112px;width:224px;height:280px;border:2px solid #fff;border-radius:6px;overflow:hidden}
.prog .ph{width:100%;height:100%}
.prog .lbl{position:absolute;left:5px;right:5px;bottom:0;height:38px;background:#fff;color:var(--ink);border-radius:6px 6px 0 0;text-align:center;font-family:"Outfit",sans-serif;font-size:16px;line-height:40px;font-weight:500}
.circle-nav{position:absolute;top:248px;width:26px;height:26px}
.programs .more{position:absolute;left:513px;top:428px}

/* shop */
.section-title{font-size:32px;font-weight:500}
.shop-card{position:absolute;width:467px;height:239px;border-radius:4px;overflow:hidden;color:var(--ink);background:linear-gradient(90deg,#d9dcd6,#eeeee0)}
.shop-card .ph{position:absolute;left:0;top:0;width:230px;height:239px}
.shop-card .txt{position:absolute;left:243px;top:52px;width:200px}
.shop-card h3{font-size:21px;font-weight:500;margin-bottom:6px}
.shop-card p{font-size:9.8px;line-height:14.5px;color:#444;margin-bottom:12px}
.shop-card .btn{height:32px;padding:0 4px 0 20px;font-size:10px}

/* blog */
.blog{position:absolute;width:306px}
.blog .ph{height:320px;border-radius:2px}
.blog .row{display:flex;justify-content:space-between;align-items:center;padding:20px 6px 0 6px}
.blog h4{font-size:15.5px;line-height:21px;font-weight:500;width:240px}
.blog .row .arr circle{fill:none;stroke:#fff;stroke-width:1.2}
.blog .row .arr path{stroke:#fff}
.blog-rule{left:120px;top:2944px;width:958px;height:1px;background:#2c3a55}

/* locations */
.loc-card{left:122px;top:3011px;width:387px;height:310px;background:var(--cream);border-radius:8px;color:var(--ink);overflow:hidden}
.loc-card h2{font-size:35px;font-weight:500;padding:18px 38px 12px}
.loc{display:flex;align-items:center;gap:14px;height:45px;padding-left:38px;font-size:13px}
.loc.active{background:var(--green);color:#fff}
.pin{width:26px;height:26px;border:1.4px solid currentColor;border-radius:50%;display:flex;align-items:center;justify-content:center}
.loc-photo{left:530px;top:3011px;width:548px;height:310px;border:4px solid var(--yellow);border-radius:8px;background:linear-gradient(180deg,#4e86cc 0%,#8bb3df 45%,#2c4f7c 62%,#1b3552 100%)}

/* newsletter */
.watermark{left:26px;top:3418px;font-family:"Outfit",sans-serif;font-weight:700;font-size:128px;letter-spacing:2px;color:#17233d;white-space:nowrap}
.news{left:350px;top:3525px;width:850px;height:321px;background:var(--yellow);color:var(--ink)}
.news h2{position:absolute;left:188px;top:92px;font-size:34px;font-weight:500}
.news p{position:absolute;left:188px;top:144px;font-size:12px}
.news .field{position:absolute;left:193px;top:177px;width:410px;height:40px;background:#fff;border:1.5px solid #222;border-radius:20px;font-size:10px;padding:0 0 0 18px;display:flex;align-items:center;justify-content:space-between}
.news .sub{height:32px;margin-right:4px;background:var(--green);color:#fff;border-radius:16px;display:flex;align-items:center;gap:14px;padding:0 4px 0 26px;font-family:"Outfit",sans-serif;font-weight:600;font-size:10px}
.news .sub .arr circle{fill:#fff}.news .sub .arr path{stroke:var(--green)}
.athlete{left:200px;top:3370px;width:230px;height:500px;border-radius:110px 110px 40px 40px;background:linear-gradient(180deg,#2b3d7a,#4a5778 40%,#c2a58c 70%,#2b3d7a)}

/* footer */
.footer{left:0;top:3846px;width:1200px;height:292px;background:var(--navy)}
.fcol{position:absolute;top:60px}
.fcol h4{font-size:15px;font-weight:500;margin-bottom:18px}
.fcol li{list-style:none;font-size:9px;line-height:20.5px;color:#d7dce6}
.fbrand{left:120px;top:60px;width:200px}
.fbrand .brand{font-size:19px;font-weight:700;margin-bottom:14px}
.fbrand p{font-size:8.2px;line-height:14.5px;color:#d7dce6}
.contact li{display:flex;align-items:center;gap:12px;line-height:36px}
.sm{width:22px;height:22px;border:1.4px solid #fff;border-radius:50%;flex:none;display:flex;align-items:center;justify-content:center}
.follow li{display:flex;align-items:center;gap:12px;line-height:36px}
.frule{position:absolute;left:120px;top:233px;width:958px;height:1px;background:#2c3a55}
.copy{position:absolute;left:120px;top:253px;font-size:8.5px;color:#d7dce6}
.legal{position:absolute;left:858px;top:253px;font-size:8.5px;color:#d7dce6;display:flex;gap:14px}
</style>
</head>
<body>

<section class="hero">
  <div class="abs" role="img" aria-label="Athlete training on gym equipment, full-width hero video" style="left:0;top:0;width:1200px;height:666px"></div>
  <h1>Unleash Your<br>Potential with<br>Corvane <em>Fitness</em></h1>
  <p>Train with elite coaches, proven programs, and a community that drives you to be your best.</p>
  <a class="btn btn-yellow b1">Explore Programs <svg class="arr" viewBox="0 0 20 20"><circle cx="10" cy="10" r="9"/><path d="M6 10h8M11 6.5 14.5 10 11 13.5"/></svg></a>
  <a class="btn btn-ghost b2">Find a gym near you <svg class="arr" viewBox="0 0 20 20"><circle cx="10" cy="10" r="9"/><path d="M6 10h8M11 6.5 14.5 10 11 13.5"/></svg></a>
  <svg class="play" viewBox="0 0 40 40"><circle cx="20" cy="20" r="20" fill="#fff"/><path d="M16 12v16l12-8z" fill="var(--yellow)"/></svg>
</section>

<header class="topbar">
  <div class="abs brand">CORVANE ATHLETICS</div>
  <nav class="nav"><span>HOME</span><span class="dd">ABOUT</span><span class="dd">PROGRAMS</span><span class="dd">SHOP</span><span class="dd">BLOG</span><span class="dd">LOCATION</span><span>CONTACT US</span></nav>
  <svg class="icon-btn" style="left:906px" viewBox="0 0 24 24"><circle cx="12" cy="9.5" r="3" fill="#fff"/><path d="M6.5 17.5c1-3 10-3 11 0" fill="#fff"/></svg>
  <svg class="icon-btn" style="left:936px" viewBox="0 0 24 24"><circle cx="11" cy="11" r="4" fill="none" stroke="#fff" stroke-width="1.6"/><path d="M14 14l3 3" stroke="#fff" stroke-width="1.6"/></svg>
  <a class="btn btn-yellow join" style="color:#fff">Join Now <svg class="arr" viewBox="0 0 20 20"><circle cx="10" cy="10" r="9" style="fill:#fff"/><path d="M6 10h8M11 6.5 14.5 10 11 13.5" style="stroke:var(--ink)"/></svg></a>
</header>

<div class="abs about-photo" role="img" aria-label="Athlete jumping rope in a training hall"></div>
<div class="abs about-card">
  <h2>About<br>Corvane Athletics</h2>
  <p>At Corvane Athletics, we believe that everyone has the power to be stronger, faster, and more resilient. Our mission is simple: to provide world-class training, expert guidance, and a supportive community that inspires you to push past limits — whether in one of our 5 state-of-the-art gyms across the U.S. or from the comfort of your home with our online programs.</p>
  <p>Founded by passionate athletes and certified trainers, Corvane Athletics started with one goal: to create a place where results, community, and experience come together.</p>
  <a class="btn btn-yellow" style="height:36px;padding:0 4px 0 20px">Meet our coaches <svg class="arr" viewBox="0 0 20 20"><circle cx="10" cy="10" r="9"/><path d="M6 10h8M11 6.5 14.5 10 11 13.5"/></svg></a>
</div>

<div class="abs features">
  <div class="feat"><div class="ring"><svg width="32" height="32" viewBox="0 0 32 32"><path d="M16 27 5 16a6 6 0 0 1 11-7 6 6 0 0 1 11 7z" fill="#fff"/></svg></div><div><h4>Community First</h4><p>Join a supportive network of motivated members.</p></div></div>
  <div class="feat"><div class="ring"><svg width="32" height="32" viewBox="0 0 32 32" fill="#fff"><circle cx="16" cy="10" r="4"/><circle cx="8" cy="13" r="3"/><circle cx="24" cy="13" r="3"/><path d="M9 25c0-6 14-6 14 0zM3 24c0-4 7-5 7-3M29 24c0-4-7-5-7-3"/></svg></div><div><h4>Expert Coaching</h4><p>Certified trainers guide you every step of the way.</p></div></div>
  <div class="feat"><div class="ring"><svg width="32" height="32" viewBox="0 0 32 32" fill="none" stroke="#fff" stroke-width="2.4" stroke-linecap="round"><path d="M16 28V8M11 12l5-5 5 5M16 18l-8-6M16 18l8-6"/></svg></div><div><h4>Flexible Options</h4><p>In-person, online, or personal coaching — train your way.</p></div></div>
  <div class="feat"><div class="ring"><svg width="32" height="32" viewBox="0 0 32 32"><path d="M6 12l4-5h12l4 5-10 13z" fill="#fff"/></svg></div><div><h4>Premium Facilities<br>&amp; Gear</h4><p>Cutting-edge equipment &amp; supplements to power your progress.</p></div></div>
</div>

<section class="abs programs">
  <h2>Featured Programs</h2>
  <svg class="circle-nav" style="left:74px" viewBox="0 0 26 26"><circle cx="13" cy="13" r="12" fill="none" stroke="#fff" stroke-width="1.4"/><path d="M18 13H8M12 9l-4 4 4 4" fill="none" stroke="#fff" stroke-width="1.6"/></svg>
  <svg class="circle-nav" style="left:1100px" viewBox="0 0 26 26"><circle cx="13" cy="13" r="12" fill="none" stroke="#fff" stroke-width="1.4"/><path d="M8 13h10M14 9l4 4-4 4" fill="none" stroke="#fff" stroke-width="1.6"/></svg>
  <div class="prog" style="left:127px"><div class="ph" role="img" aria-label="Masters athletes training" style="background:linear-gradient(170deg,#5a5e66,#22262e)"></div><div class="lbl">Masters</div></div>
  <div class="prog" style="left:368px"><div class="ph" role="img" aria-label="Athlete running in a gym" style="background:linear-gradient(170deg,#6a6d72,#2e3036)"></div><div class="lbl">Functional Fitness</div></div>
  <div class="prog" style="left:612px"><div class="ph" role="img" aria-label="Athlete lifting a loaded barbell" style="background:linear-gradient(170deg,#4c5664,#1d2430)"></div><div class="lbl">Competitive</div></div>
  <div class="prog" style="left:854px"><div class="ph" role="img" aria-label="Bowl of fresh salad held in hands" style="background:linear-gradient(170deg,#3c3f3e,#4f7a2c 55%,#2a2d2c)"></div><div class="lbl">Nutrition</div></div>
  <a class="btn btn-ghost more" style="height:38px;padding:0 4px 0 18px">Explore Programs <svg class="arr" viewBox="0 0 20 20"><circle cx="10" cy="10" r="9"/><path d="M6 10h8M11 6.5 14.5 10 11 13.5"/></svg></a>
</section>

<h2 class="abs section-title" style="left:121px;top:1843px">Shop Corvane Gear + Supplements</h2>
<a class="abs btn btn-ghost" style="left:953px;top:1845px;height:38px;padding:0 4px 0 26px">View All <svg class="arr" viewBox="0 0 20 20"><circle cx="10" cy="10" r="9"/><path d="M6 10h8M11 6.5 14.5 10 11 13.5"/></svg></a>

<div class="shop-card" style="left:122px;top:1916px"><div class="ph" role="img" aria-label="Yoga mat, water bottle and gloves" style="background:linear-gradient(120deg,#cfd8a0,#b8d23e 50%,#dcded2)"></div><div class="txt"><h3>Merch</h3><p>Lorem ipsum dolor sit amet, consectetur adipiscing elit, sed do eiusmod tempor incididunt cumsan lacus vel facilisis.</p><a class="btn btn-yellow">Shop Now <svg class="arr" viewBox="0 0 20 20"><circle cx="10" cy="10" r="9"/><path d="M6 10h8M11 6.5 14.5 10 11 13.5"/></svg></a></div></div>
<div class="shop-card" style="left:610px;top:1916px;background:linear-gradient(90deg,#e2e4e2,#e8ece8)"><div class="ph" role="img" aria-label="Supplement capsules spilling from a bottle" style="background:linear-gradient(120deg,#e8e8e4,#bfe3ea 55%,#dfe2e0)"></div><div class="txt"><h3>Supplements</h3><p>Lorem ipsum dolor sit amet, consectetur adipiscing elit, sed do eiusmod tempor incididunt cumsan lacus vel facilisis.</p><a class="btn btn-yellow">Shop Now <svg class="arr" viewBox="0 0 20 20"><circle cx="10" cy="10" r="9"/><path d="M6 10h8M11 6.5 14.5 10 11 13.5"/></svg></a></div></div>
<div class="shop-card" style="left:122px;top:2168px;background:linear-gradient(90deg,#e1e3e2,#e7e9e4)"><div class="ph" role="img" aria-label="Ab roller, dumbbells and water bottle" style="background:linear-gradient(120deg,#dde0e0,#4a6fc9 55%,#e0e2e0)"></div><div class="txt"><h3>Equipment</h3><p>Lorem ipsum dolor sit amet, consectetur adipiscing elit, sed do eiusmod tempor incididunt cumsan lacus vel facilisis.</p><a class="btn btn-yellow">Shop Now <svg class="arr" viewBox="0 0 20 20"><circle cx="10" cy="10" r="9"/><path d="M6 10h8M11 6.5 14.5 10 11 13.5"/></svg></a></div></div>
<div class="shop-card" style="left:610px;top:2168px;background:linear-gradient(90deg,#dfe3e3,#eceadb)"><div class="ph" role="img" aria-label="Sports top, earphones and bottle" style="background:linear-gradient(120deg,#dfe4e4,#3f9aa6 45%,#5b6068 60%,#dfe2e0)"></div><div class="txt"><h3>Apparel</h3><p>Lorem ipsum dolor sit amet, consectetur adipiscing elit, sed do eiusmod tempor incididunt cumsan lacus vel facilisis.</p><a class="btn btn-yellow">Shop Now <svg class="arr" viewBox="0 0 20 20"><circle cx="10" cy="10" r="9"/><path d="M6 10h8M11 6.5 14.5 10 11 13.5"/></svg></a></div></div>

<h2 class="abs section-title" style="left:119px;top:2467px">Latest Blog &amp; Resources</h2>
<a class="abs btn btn-yellow" style="left:932px;top:2469px;height:38px;padding:0 4px 0 22px">View All Blog <svg class="arr" viewBox="0 0 20 20"><circle cx="10" cy="10" r="9" style="fill:var(--band)"/><path d="M6 10h8M11 6.5 14.5 10 11 13.5"/></svg></a>

<article class="blog" style="left:120px;top:2539px"><div class="ph" role="img" aria-label="Two athletes training together" style="background:linear-gradient(170deg,#6b6860,#2a2b2e)"></div><div class="row"><h4>How to Fix the Dreaded Elbow Rebend in Your Jerk</h4><svg class="arr" viewBox="0 0 20 20"><circle cx="10" cy="10" r="9"/><path d="M6 10h8M11 6.5 14.5 10 11 13.5"/></svg></div></article>
<article class="blog" style="left:446px;top:2539px"><div class="ph" role="img" aria-label="Athlete skipping rope in a gym" style="background:linear-gradient(170deg,#3a3e46,#121419)"></div><div class="row"><h4>Tips To Avoid Injury During Workouts</h4><svg class="arr" viewBox="0 0 20 20"><circle cx="10" cy="10" r="9"/><path d="M6 10h8M11 6.5 14.5 10 11 13.5"/></svg></div></article>
<article class="blog" style="left:771px;top:2539px"><div class="ph" role="img" aria-label="Athlete running across a gym floor" style="background:linear-gradient(170deg,#74767a,#393b40)"></div><div class="row"><h4>Maximize Your Potential as a CrossTrain Masters Athlete</h4><svg class="arr" viewBox="0 0 20 20"><circle cx="10" cy="10" r="9"/><path d="M6 10h8M11 6.5 14.5 10 11 13.5"/></svg></div></article>
<div class="abs blog-rule"></div>

<div class="abs loc-card">
  <h2>Our Locations</h2>
  <div class="loc active"><span class="pin"><svg width="12" height="14" viewBox="0 0 12 14"><path d="M6 13S1.5 8 1.5 5a4.5 4.5 0 0 1 9 0C10.5 8 6 13 6 13z" fill="none" stroke="currentColor" stroke-width="1.3"/><circle cx="6" cy="5" r="1.5" fill="currentColor"/></svg></span>San Diego (HQ)</div>
  <div class="loc"><span class="pin"><svg width="12" height="14" viewBox="0 0 12 14"><path d="M6 13S1.5 8 1.5 5a4.5 4.5 0 0 1 9 0C10.5 8 6 13 6 13z" fill="none" stroke="currentColor" stroke-width="1.3"/><circle cx="6" cy="5" r="1.5" fill="currentColor"/></svg></span>Boston</div>
  <div class="loc"><span class="pin"><svg width="12" height="14" viewBox="0 0 12 14"><path d="M6 13S1.5 8 1.5 5a4.5 4.5 0 0 1 9 0C10.5 8 6 13 6 13z" fill="none" stroke="currentColor" stroke-width="1.3"/><circle cx="6" cy="5" r="1.5" fill="currentColor"/></svg></span>Miami</div>
  <div class="loc"><span class="pin"><svg width="12" height="14" viewBox="0 0 12 14"><path d="M6 13S1.5 8 1.5 5a4.5 4.5 0 0 1 9 0C10.5 8 6 13 6 13z" fill="none" stroke="currentColor" stroke-width="1.3"/><circle cx="6" cy="5" r="1.5" fill="currentColor"/></svg></span>Seattle</div>
  <div class="loc"><span class="pin"><svg width="12" height="14" viewBox="0 0 12 14"><path d="M6 13S1.5 8 1.5 5a4.5 4.5 0 0 1 9 0C10.5 8 6 13 6 13z" fill="none" stroke="currentColor" stroke-width="1.3"/><circle cx="6" cy="5" r="1.5" fill="currentColor"/></svg></span>DC</div>
</div>
<div class="abs loc-photo" role="img" aria-label="San Diego city skyline across the bay"></div>

<div class="abs watermark">CORVANE ATHLETICS</div>
<section class="abs news">
  <h2>Stay Connected with Corvane</h2>
  <p>Get exclusive workouts, nutrition advice, and updates.</p>
  <div class="field"><span>Enter Your Email</span><span class="sub">SUBSCRIBE <svg class="arr" viewBox="0 0 20 20"><circle cx="10" cy="10" r="9"/><path d="M6 10h8M11 6.5 14.5 10 11 13.5"/></svg></span></div>
</section>
<div class="abs athlete" role="img" aria-label="Athlete lifting a barbell overhead"></div>

<footer class="abs footer">
  <div class="fcol fbrand"><div class="brand">CORVANE ATHLETICS</div><p>At Corvane Athletics, we believe that everyone has the power to be stronger, faster, and more resilient. Our mission is simple: to provide world-class training, expert guidance, and a supportive community that inspires you to push past limits — whether in one of our 5 state-of-the-art gyms across the U.S.</p></div>
  <div class="fcol contact" style="left:358px"><h4>Contact Us</h4><ul>
    <li><span class="sm"><svg width="11" height="11" viewBox="0 0 12 12"><path d="M2 1.5l2.5-.5 1 2.5-1.3 1a6 6 0 0 0 3.3 3.3l1-1.3 2.5 1-.5 2.5C5.5 10.5 1.5 6.5 2 1.5z" fill="#fff"/></svg></span>800-555-0147</li>
    <li><span class="sm"><svg width="11" height="11" viewBox="0 0 12 12"><rect x="1" y="2.5" width="10" height="7" rx="1" fill="none" stroke="#fff" stroke-width="1.2"/><path d="M1.5 3l4.5 3.5L10.5 3" fill="none" stroke="#fff" stroke-width="1.2"/></svg></span><span style="color:var(--yellow)">hello@corvaneathletics.example</span></li></ul></div>
  <div class="fcol" style="left:559px"><h4>Main Link</h4><ul><li>Home</li><li>About</li><li>Programs</li><li>Blog</li><li>Location</li><li>Contact Us</li></ul></div>
  <div class="fcol" style="left:699px"><h4>Our Location</h4><ul><li>San Diego (HQ)</li><li>Boston</li><li>Miami</li><li>Seattle</li><li>DC</li></ul></div>
  <div class="fcol" style="left:869px"><h4>Shop</h4><ul><li>Merch</li><li>Apparel</li><li>Equipment</li><li>Supplements</li><li>PDFs</li><li>Programs</li></ul></div>
  <div class="fcol follow" style="left:997px"><h4>Follow Us</h4><ul><li><span class="sm"></span>Pulse</li><li><span class="sm"></span>Chirp</li><li><span class="sm"></span>Snapshot</li><li><span class="sm"></span>Reelcast</li></ul></div>
  <div class="frule"></div>
  <div class="copy">© 2025 Corvane Athletics All Rights Reserved.</div>
  <div class="legal"><span>Privacy</span><span>|</span><span>Cookies/Terms</span><span>|</span><span>Conditions</span></div>
</footer>

</body>
</html>
```